Design a Pulsebox Flyer to attract new membership

With constantly updating workouts and the nutritional help Tellmore LiftWorks is more than just an average gym. It’s a place for everyone to get healthy in a stress-free, safe and friendly environment.

Target Market(s)

Women ages 25-60 years old

Industry/Entity Type

Environment

Font styles to use
Serif

Requirements
Must have
• Please read thru the following info before you begin your design:
• Pulsebox Flyer Information
• Please keep in mind a few things:
• 1) Our facility colors orange and green (you can see from my website what the color scheme is)
• 2) Our target demo graphic is women between the ages of 25-60, a large majority of my current clientele are middle aged women 45-60 years old
• 3) Try to keep it clean, and white (like Quintrel's website) if possible
• Side 1: (image of equipment and a younger women working out)
• 1) TLLW Logo
• 2) FREE WEEK TRIAL (big font) Sing up at www.tlliftworks.example/schedulesign-up
• 3) Schedule: Monday-Friday 5:30am – 6:15am – 6:00pm – 7:00pm
• 4) Rates: $150/ Month Unlimited Classes - $100 /10 session package
• *15% discount for all fire, police, military, veterans, teachers, current students & trade association members
• 5) Address: 917 Quill Avenue Staten Island, NY 10304
• 6) Contact info: Phone: 347-555-0182 Email: tlliftworks@mailbox.example
• 7) Website and Social media www.tlliftworks.example find us @TLLiftWorks on Friendloop, Chirpline, Snapgrid, Rateo, Orbix + and spotkeeper
• Side 2 (image of a women working out, preferable middle aged):
• 1) 6 Benefits of PulseBox:
• a. Benefit #1: It BLASTS calories
• b. Benefit #2: It’s great Cardiovascular conditioning
• c. Benefit #3: It increases joint mobility
• d. Benefit #4: Everyday is something different, guaranteed
• e. Benefit #5: You’ll make new friends
• f. Benefit #6: You’ll feel like a badass
• 2) Free Week Trial Class (smaller font at the bottom) sign up at: www.tlliftworks.example/schedulesign-up

```html
<!DOCTYPE html>
<html lang="en">
<head>
<meta charset="utf-8">
<title>Free Week Trial Flyer – Tellmore LiftWorks</title>
<link rel="stylesheet" href="https://fonts.googleapis.com/css2?family=PT+Sans:wght@400;700&family=PT+Sans+Narrow:wght@400;700&display=swap">
<style>
  :root {
    --green: #2f6b3a;
    --green-dark: #24552d;
    --orange: #f0a11b;
    --ink: #2b2b2b;
    --white: #ffffff;
    --photo-light: #cfd3d6;
    --photo-dark: #6f7880;
    --social: #3b6fb0;
  }
  * { margin: 0; padding: 0; box-sizing: border-box; }
  html, body { width: 847px; height: 1200px; overflow: hidden; background: var(--white); }
  body { font-family: "PT Sans", Arial, sans-serif; color: var(--ink); }
  .flyer { position: relative; width: 847px; height: 1200px; background: var(--white); overflow: hidden; }

  .headline { position: absolute; top: 16px; left: 0; width: 100%; text-align: center; }
  .headline-lead { font-weight: 700; font-size: 42px; line-height: 44px; color: var(--green); letter-spacing: 1px; }
  .headline-main { font-weight: 700; font-size: 112px; line-height: 98px; color: var(--orange); letter-spacing: 2px; }
  .signup-label { font-size: 27px; line-height: 30px; color: var(--green-dark); margin-top: 2px; }
  .signup-url { font-family: "PT Sans Narrow", Arial, sans-serif; font-weight: 700; font-size: 38px; line-height: 42px; color: var(--green-dark); }

  .schedule-band { position: absolute; top: 236px; left: 0; width: 100%; height: 38px; background: var(--green); color: var(--white); text-align: center; font-size: 24px; line-height: 38px; }

  .hero-photo { position: absolute; top: 274px; left: 0; width: 847px; height: 536px; background: linear-gradient(160deg, var(--photo-light) 0%, #aab1b6 45%, var(--photo-dark) 100%); }

  .discount-badge { position: absolute; top: 684px; left: 700px; width: 92px; height: 92px; border-radius: 50%; background: var(--orange); color: var(--white); text-align: center; transform: rotate(-12deg); }
  .discount-badge .value { display: block; font-weight: 700; font-size: 36px; line-height: 1; padding-top: 20px; }
  .discount-badge .label { display: block; font-size: 11px; letter-spacing: 1px; }

  .discount-note { position: absolute; top: 820px; left: 0; width: 100%; text-align: center; font-family: "PT Sans Narrow", Arial, sans-serif; font-size: 16px; line-height: 20px; color: var(--ink); }

  .rates { position: absolute; top: 852px; left: 0; width: 100%; text-align: center; color: var(--ink); }
  .rate-line { font-size: 34px; line-height: 40px; }
  .rate-line strong { font-weight: 700; }

  .contact-band { position: absolute; top: 964px; left: 0; width: 100%; height: 126px; background: var(--orange); }
  .brand-box { position: absolute; top: 950px; left: 22px; width: 176px; height: 140px; background: var(--green); display: flex; align-items: center; justify-content: center; text-align: center; }
  .brand-name { font-weight: 700; font-size: 24px; line-height: 1.1; color: var(--white); }
  .contact-details { position: absolute; top: 974px; left: 214px; width: 620px; color: var(--white); font-family: "PT Sans Narrow", Arial, sans-serif; font-style: normal; font-size: 24px; line-height: 36px; white-space: nowrap; }
  .contact-details .phone, .contact-details .email { font-weight: 700; font-size: 27px; }

  .social { position: absolute; top: 1136px; left: 0; width: 100%; display: flex; align-items: center; justify-content: center; gap: 10px; }
  .social-label { font-size: 22px; color: var(--ink); margin-right: 6px; }
  .social-dot { width: 40px; height: 40px; border-radius: 50%; background: var(--social); }
</style>
</head>
<body>
<main class="flyer">
  <header class="headline">
    <div class="headline-lead">FREE WEEK</div>
    <div class="headline-main">TRIAL</div>
    <div class="signup-label">Sing up at</div>
    <div class="signup-url">www.tlliftworks.example/schedulesign-up</div>
  </header>

  <div class="schedule-band">Monday-Friday 5:30am – 6:15am – 6:00pm – 7:00pm</div>

  <div class="hero-photo" role="img" aria-label="Photo of a woman doing a push-up on dumbbells in a gym with equipment behind her"></div>

  <div class="discount-badge"><span class="value">%15</span><span class="label">DISCOUNT</span></div>

  <p class="discount-note">15% discount for all fire, police, military, veterans, teachers, current students &amp; trade association members</p>

  <section class="rates">
    <div class="rate-line"><strong>$150/</strong> MONTH <strong>UNLIMITED CLASSES</strong></div>
    <div class="rate-line">$100 /10 <strong>SESSION</strong> PACKAGE</div>
  </section>

  <div class="contact-band"></div>
  <div class="brand-box"><span class="brand-name">Tellmore<br>LiftWorks</span></div>
  <address class="contact-details">
    917 Quill Avenue Staten Island, NY 10304<br>
    Phone: <span class="phone">347-555-0182</span>&nbsp; Email: <span class="email">tlliftworks@mailbox.example</span><br>
    www.tlliftworks.example
  </address>

  <footer class="social">
    <span class="social-label">Find us @TLLiftWorks on</span>
    <span class="social-dot" aria-label="Friendloop"></span>
    <span class="social-dot" aria-label="Chirpline"></span>
    <span class="social-dot" aria-label="Snapgrid"></span>
    <span class="social-dot" aria-label="Rateo"></span>
    <span class="social-dot" aria-label="Orbix +"></span>
    <span class="social-dot" aria-label="spotkeeper"></span>
  </footer>
</main>
</body>
</html>
```